Bran-well Tide Gate Custom Brokers Limited

Name: Lorvina Hadcott
Title: Customs Broker
Address: Shop 9 Ferncliff Commercial Complex
207-209 Mulgrave Road
Kingston 8
Telephone: (876)
Email: tidegatewell@mailbrook.example

```html
<!DOCTYPE html>
<html lang="en">
<head>
<meta charset="utf-8">
<title>Bran-well Tide Gate Custom Brokers Limited – Business Card</title>
<link rel="stylesheet" href="https://fonts.googleapis.com/css2?family=Poppins:wght@400;500;600;800&display=swap">
<style>
  :root {
    --navy: #0b2b52;
    --gold: #e9a80c;
    --white: #ffffff;
    --stage: #2a2a2c;
    --muted: #9aa3ad;
  }
  * { margin: 0; padding: 0; box-sizing: border-box; }
  html, body { width: 1200px; height: 1200px; overflow: hidden; }
  body {
    background: var(--stage);
    font-family: "Poppins", sans-serif;
    display: flex;
    flex-direction: column;
    align-items: center;
    justify-content: center;
    gap: 40px;
  }
  .card {
    position: relative;
    width: 960px;
    height: 548px;
    overflow: hidden;
  }

  /* Back side */
  .card-back {
    background: var(--navy);
    display: flex;
    align-items: center;
    justify-content: center;
  }
  .brand {
    display: flex;
    align-items: center;
    gap: 22px;
  }
  .brand-dot {
    width: 34px;
    height: 34px;
    border-radius: 50%;
    background: var(--gold);
    flex: none;
  }
  .brand-name {
    font-weight: 600;
    letter-spacing: 0.04em;
    line-height: 1.2;
  }
  .card-back .brand-name { color: var(--white); font-size: 40px; }

  /* Front side */
  .card-front { background: var(--white); }
  .front-swoosh {
    position: absolute;
    inset: 0;
    width: 100%;
    height: 100%;
  }
  .front-content {
    position: absolute;
    left: 56px;
    top: 58px;
    width: 560px;
    color: var(--navy);
  }
  .card-front .brand { gap: 16px; margin-bottom: 44px; }
  .card-front .brand-dot { width: 26px; height: 26px; }
  .card-front .brand-name { color: var(--navy); font-size: 30px; }
  .person-name {
    font-weight: 800;
    font-size: 38px;
    line-height: 1.1;
    letter-spacing: 0.01em;
  }
  .person-title {
    color: var(--gold);
    font-size: 27px;
    font-weight: 500;
    margin-bottom: 18px;
  }
  .address {
    font-style: normal;
    font-size: 24px;
    font-weight: 500;
    line-height: 1.35;
    margin-bottom: 14px;
  }
  .contact-list { list-style: none; font-size: 24px; font-weight: 500; }
  .contact-item {
    display: flex;
    align-items: center;
    gap: 14px;
    line-height: 1.45;
  }
  .contact-icon { width: 26px; height: 26px; flex: none; }
</style>
</head>
<body>

  <section class="card card-back" aria-label="Card back">
    <div class="brand">
      <span class="brand-dot"></span>
      <p class="brand-name">Bran-well Tide Gate<br>Custom Brokers Limited</p>
    </div>
  </section>

  <section class="card card-front" aria-label="Card front">
    <svg class="front-swoosh" viewBox="0 0 960 548" preserveAspectRatio="none" aria-hidden="true">
      <path fill="var(--navy)" d="M560 0 C770 40 940 250 850 440 C815 500 765 530 700 548 L960 548 L960 0 Z"/>
      <path fill="none" stroke="var(--gold)" stroke-width="8" stroke-linecap="round"
            d="M420 0 C690 30 885 230 815 430 C790 495 745 528 660 548"/>
    </svg>

    <div class="front-content">
      <div class="brand">
        <span class="brand-dot"></span>
        <p class="brand-name">Bran-well Tide Gate<br>Custom Brokers Limited</p>
      </div>

      <h1 class="person-name">LORVINA HADCOTT</h1>
      <p class="person-title">Customs Broker</p>

      <address class="address">
        Shop 9 Ferncliff Commercial Complex<br>
        207-209 Mulgrave Road, Kingston 8
      </address>

      <ul class="contact-list">
        <li class="contact-item">
          <svg class="contact-icon" viewBox="0 0 26 26" aria-hidden="true">
            <circle cx="13" cy="13" r="13" fill="var(--gold)"/>
            <rect x="8" y="6" width="10" height="14" rx="2" fill="none" stroke="var(--white)" stroke-width="2"/>
          </svg>
          (876) 555 014 2231
        </li>
        <li class="contact-item">
          <svg class="contact-icon" viewBox="0 0 26 26" aria-hidden="true">
            <circle cx="13" cy="13" r="13" fill="var(--gold)"/>
            <rect x="6" y="8" width="14" height="10" rx="1" fill="none" stroke="var(--white)" stroke-width="1.8"/>
            <path d="M6 8 L13 14 L20 8" fill="none" stroke="var(--white)" stroke-width="1.8"/>
          </svg>
          tidegatewell@mailbrook.example
        </li>
      </ul>
    </div>
  </section>

</body>
</html>
```